Corvelle Meadow Organic Flower Farm, Farmer Florist

I am a flower grower and florist, so I do everything from the field to the vase. I want to include my website, phone, email and instagram

```html
<!DOCTYPE html>
<html lang="en">
<head>
<meta charset="utf-8">
<title>Corvelle Meadow – Business Card</title>
<link href="https://fonts.googleapis.com/css2?family=Cinzel:wght@500&family=Marcellus&family=Arimo:wght@400&display=swap" rel="stylesheet">
<style>
  :root {
    --backdrop: #a9a9a9;
    --card-light: #ffffff;
    --card-dark: #000000;
    --maroon: #4e1f27;
    --maroon-muted: #5a2a33;
    --blush: #f08a8e;
    --ink: #444444;
    --rule: #c9c9c9;
  }
  * { margin: 0; padding: 0; box-sizing: border-box; }
  html, body { width: 1200px; height: 900px; overflow: hidden; }
  body { background: var(--backdrop); position: relative; font-family: "Arimo", Arial, sans-serif; }

  .card {
    position: absolute;
    width: 459px;
    height: 283px;
    border-radius: 14px;
    box-shadow: 2px 3px 4px rgba(0,0,0,0.45);
    overflow: hidden;
  }
  .card--front { left: 137px; top: 265px; background: var(--card-light); }
  .card--back  { left: 625px; top: 268px; background: var(--card-dark); }

  .brand {
    position: absolute;
    display: flex;
    flex-direction: column;
    align-items: center;
    transform: translateX(-50%);
  }
  .brand__dot { border-radius: 50%; background: var(--blush); }
  .brand__name { font-family: "Marcellus", serif; letter-spacing: 0.06em; line-height: 1; }

  .card--front .brand { left: 122px; top: 96px; }
  .card--front .brand__dot { width: 26px; height: 26px; margin-bottom: 20px; }
  .card--front .brand__name { font-size: 30px; color: var(--maroon); }

  .card--back .brand { left: 230px; top: 92px; }
  .card--back .brand__dot { width: 34px; height: 34px; margin-bottom: 24px; }
  .card--back .brand__name { font-size: 38px; color: var(--maroon-muted); }

  .divider {
    position: absolute; left: 236px; top: 85px;
    width: 1px; height: 110px; background: var(--rule);
  }

  .contact { position: absolute; left: 252px; top: 90px; color: var(--ink); }
  .contact__name {
    font-family: "Cinzel", serif; font-weight: 500;
    font-size: 17px; color: var(--maroon); letter-spacing: 0.02em; line-height: 1.1;
  }
  .contact__role { font-size: 12.5px; margin-top: 2px; }
  .contact__list { list-style: none; margin-top: 20px; font-size: 12.5px; }
  .contact__item { display: flex; align-items: center; gap: 5px; height: 17px; }
  .contact__icon { width: 11px; height: 11px; fill: var(--maroon); flex: none; }

  .social {
    position: absolute; left: 134px; top: 221px;
    width: 203px; height: 22px;
    display: flex; align-items: center; gap: 8px;
  }
  .social__rule { flex: 1; height: 1px; background: var(--rule); }
  .social__mark { width: 22px; height: 22px; border-radius: 50%; background: var(--blush); }
</style>
</head>
<body>

<section class="card card--front">
  <div class="brand">
    <span class="brand__dot"></span>
    <span class="brand__name">CORVELLE</span>
  </div>

  <div class="divider"></div>

  <div class="contact">
    <p class="contact__name">ELISE MARROW</p>
    <p class="contact__role">Managing Director</p>
    <ul class="contact__list">
      <li class="contact__item">
        <svg class="contact__icon" viewBox="0 0 24 24" aria-hidden="true"><path d="M6.6 10.8a15 15 0 0 0 6.6 6.6l2.2-2.2a1 1 0 0 1 1-.25 11.4 11.4 0 0 0 3.6.57 1 1 0 0 1 1 1V20a1 1 0 0 1-1 1A17 17 0 0 1 3 4a1 1 0 0 1 1-1h3.5a1 1 0 0 1 1 1c0 1.25.2 2.45.57 3.57a1 1 0 0 1-.25 1z"/></svg>
        044-987 654 321
      </li>
      <li class="contact__item">
        <svg class="contact__icon" viewBox="0 0 24 24" aria-hidden="true"><path d="M2 5h20v14H2z M3 6l9 7 9-7" stroke="#fff" stroke-width="1.5"/></svg>
        hello@corvellemeadow.com
      </li>
      <li class="contact__item">
        <svg class="contact__icon" viewBox="0 0 24 24" aria-hidden="true"><circle cx="12" cy="12" r="10" fill="none" stroke="#4e1f27" stroke-width="2"/><path d="M2 12h20M12 2c3 3 3 17 0 20M12 2c-3 3-3 17 0 20" fill="none" stroke="#4e1f27" stroke-width="1.6"/></svg>
        www.corvellemeadow.com
      </li>
    </ul>
  </div>

  <div class="social">
    <span class="social__rule"></span>
    <span class="social__mark"></span>
    <span class="social__rule"></span>
  </div>
</section>

<section class="card card--back">
  <div class="brand">
    <span class="brand__dot"></span>
    <span class="brand__name">CORVELLE</span>
  </div>
</section>

</body>
</html>
```